Mindfulness School for Children -- Business Cards

We're looking for business cards for our school directors and owners. We're a mindfulness school for children called little lanterns. Attached are our logos/icons.

```html
<!DOCTYPE html>
<html lang="en">
<head>
<meta charset="utf-8">
<title>little lanterns — Business Cards</title>
<link rel="stylesheet" href="https://fonts.googleapis.com/css2?family=Alegreya:wght@400&family=Arimo:wght@400&display=swap">
<style>
  :root {
    --backdrop: #232323;
    --card: #0b0b0b;
    --card-edge: #161616;
    --teal: #6ab8c4;
    --mint: #76c2a0;
    --ink-light: #f2f2f2;
    --divider: #4a4a4a;
  }
  * { margin: 0; padding: 0; box-sizing: border-box; }
  html, body {
    width: 1200px; height: 900px; overflow: hidden;
    background: var(--backdrop);
  }
  .stage {
    width: 1200px; height: 900px;
    display: flex; align-items: center; justify-content: center; gap: 40px;
  }
  .card {
    position: relative;
    width: 540px; height: 309px;
    background: var(--card);
    border: 1px solid var(--card-edge);
    box-shadow: 0 14px 34px rgba(0,0,0,.55);
  }
  .wordmark {
    font-family: "Alegreya", Georgia, serif;
    font-weight: 400;
    color: var(--teal);
    letter-spacing: .5px;
    white-space: nowrap;
  }
  /* contact side */
  .card--contact .wordmark {
    position: absolute; left: 34px; top: 168px;
    font-size: 34px;
  }
  .card--contact .divider {
    position: absolute; left: 258px; top: 58px;
    width: 1px; height: 168px; background: var(--divider);
  }
  .details {
    position: absolute; left: 282px; top: 58px;
    font-family: "Arimo", Arial, sans-serif;
    color: var(--ink-light);
  }
  .details__name {
    font-family: "Alegreya", Georgia, serif;
    font-size: 26px; color: var(--teal); line-height: 1;
  }
  .details__role { font-size: 14px; margin-top: 4px; }
  .details__list { list-style: none; margin-top: 16px; }
  .details__list li {
    display: flex; align-items: center; gap: 8px;
    font-size: 13.5px; line-height: 21px;
  }
  .details__list svg { width: 13px; height: 13px; flex: none; }
  .details__site-name { color: var(--mint); }
  .details__address { font-size: 13.5px; line-height: 19px; margin-top: 12px; padding-left: 21px; }
  /* logo side */
  .card--brand { display: flex; align-items: center; justify-content: center; }
  .card--brand .wordmark { font-size: 50px; }
</style>
</head>
<body>
<main class="stage">
  <section class="card card--contact">
    <div class="wordmark">little lanterns</div>
    <div class="divider"></div>
    <div class="details">
      <p class="details__name">Daniel Harper</p>
      <p class="details__role">Managing Director</p>
      <ul class="details__list">
        <li>
          <svg viewBox="0 0 16 16" aria-hidden="true"><path d="M4 1.5l2.2 3-1.3 1.6c.9 2 2.4 3.5 4.4 4.4l1.6-1.3 3 2.2-1.4 2.6C7 13.6 2.4 9 1.4 3z" fill="var(--teal)"/></svg>
          044-555 018 204
        </li>
        <li>
          <svg viewBox="0 0 16 16" aria-hidden="true"><rect x="1" y="3" width="14" height="10" fill="var(--teal)"/><path d="M1 3l7 6 7-6" fill="none" stroke="var(--card)" stroke-width="1.3"/></svg>
          hello@littlelanterns.org
        </li>
        <li>
          <svg viewBox="0 0 16 16" aria-hidden="true"><g fill="none" stroke="var(--teal)" stroke-width="1.3"><circle cx="8" cy="8" r="6.5"/><ellipse cx="8" cy="8" rx="3" ry="6.5"/><path d="M1.5 8h13M2.5 4.8h11M2.5 11.2h11"/></g></svg>
          <span>www.<span class="details__site-name">littlelanterns</span>.org</span>
        </li>
      </ul>
      <p class="details__address">18 Willow Lane, Maple Court<br>20417, Harbour Town</p>
    </div>
  </section>

  <section class="card card--brand">
    <div class="wordmark">little lanterns</div>
  </section>
</main>
</body>
</html>
```